Single-sided business card for restaurant velmora with new logo made on this site

Business card options with new logo including restaurant name, address, phone number and website. This business card is single-sided only and will be presented at the hostess desk for clients to take. I would like to see options based on a cream card background, a white card background, a yellow card background and a burgundy colored background. It needs to be elegant and traditional.

Target Market(s)

local and international crowd

Industry/Entity Type

restaurant

Contact Information for Business Card

address, website and phone number

Font styles to use
Serif

Colors
EE7325
F08F49
F5BC92
FAE3D3
FDF4ED

Requirements
Must have
• new logo, address, phone number, website
Should not have
• more than three colors

```html
<!DOCTYPE html>
<html lang="es">
<head>
<meta charset="utf-8">
<title>Velmora – Tarjeta de presentación</title>
<link href="https://fonts.googleapis.com/css2?family=Tinos:wght@400;700&display=swap" rel="stylesheet">
<style>
  :root {
    --stage: #d6d6d8;
    --burgundy: #35171b;
    --burgundy-deep: #24100f;
    --gold: #f2a51e;
    --ivory: #f7f2ec;
    --rose: #d9636c;
  }
  * { box-sizing: border-box; margin: 0; padding: 0; }
  html, body {
    width: 1200px;
    height: 800px;
    overflow: hidden;
    background: var(--stage);
  }
  .stage {
    width: 1200px;
    height: 800px;
    display: flex;
    align-items: center;
    justify-content: center;
  }
  .card {
    position: relative;
    width: 1000px;
    height: 572px;
    background: var(--burgundy);
    border: 3px solid var(--gold);
    border-radius: 40px;
    overflow: hidden;
    font-family: "Tinos", "Times New Roman", serif;
  }
  .card__artwork {
    position: absolute;
    left: 380px;
    top: -40px;
    width: 680px;
    height: 620px;
    background:
      radial-gradient(ellipse 60% 45% at 30% 78%, rgba(217, 99, 108, 0.85), rgba(217, 99, 108, 0) 70%),
      radial-gradient(ellipse 55% 60% at 70% 40%, rgba(20, 8, 8, 0.9), rgba(20, 8, 8, 0) 72%),
      radial-gradient(ellipse 70% 65% at 50% 55%, rgba(120, 45, 52, 0.7), rgba(53, 23, 27, 0) 75%);
  }
  .brand {
    position: absolute;
    left: 70px;
    top: 120px;
    display: flex;
    align-items: flex-end;
    gap: 22px;
  }
  .brand__mark {
    width: 104px;
    height: 104px;
    background: var(--gold);
  }
  .brand__name {
    color: var(--ivory);
    font-weight: 400;
    font-size: 46px;
    letter-spacing: 0.16em;
    line-height: 1;
    padding-bottom: 2px;
  }
  .details {
    position: absolute;
    left: 70px;
    top: 270px;
    color: var(--ivory);
    font-size: 25px;
    line-height: 1.22;
  }
  .details__label {
    color: var(--gold);
    font-weight: 700;
  }
  .details__address { margin-bottom: 18px; }
  .details__phone {
    display: flex;
    align-items: center;
    gap: 8px;
    font-size: 30px;
  }
  .details__phone svg { width: 24px; height: 24px; }
  .details__web {
    margin-top: 20px;
    color: var(--gold);
    font-weight: 700;
  }
</style>
</head>
<body>
  <main class="stage">
    <article class="card">
      <div class="card__artwork" role="img" aria-label="Ilustración de hojas de agave en tonos rosa y burdeos"></div>

      <header class="brand">
        <span class="brand__mark"></span>
        <span class="brand__name">VELMORA</span>
      </header>

      <section class="details">
        <p class="details__label">Restaurant Velmora</p>
        <p class="details__address">Calle Jazmín 418<br>Bahía Serena<br>Oaxaca CP 70412</p>
        <p class="details__label">Reservaciones</p>
        <p class="details__phone">
          <svg viewBox="0 0 24 24" fill="none" stroke="currentColor" stroke-width="1.6" aria-hidden="true">
            <path d="M6.5 3.5l3 3.2-1.8 2.4c1.2 2.6 3.2 4.6 5.8 5.8l2.4-1.8 3.2 3-1.6 2.9c-7.3-.6-13-6.3-13.6-13.6z"/>
          </svg>
          958-555-0142
        </p>
        <p class="details__web">Velmora.com.mx</p>
      </section>
    </article>
  </main>
</body>
</html>
```